Develop A Dynamic, Professional Powerpoint Design Template

We need a dynamic powerpoint design for a new company that designs novel product packaging. We would like to see designs that use the color black and blue. The final design should communicate "change" and "transitions". See attachments for inspiration on graphics that inspire us.

We like these colors:
Black
Blue
Green
Orange

Reason: We need to extend this contest to allow for the inclusion of our final logo design which is expected to be completed tomorrow, 10/28/2015.

Target Market(s)

High end clients.

Industry/Entity Type

It Company

Font styles to use
Serif

Requirements
Must have
• See "example" slides for type of information that we will be presenting. The name of our company is "Bramblecrest Carton Works". This template will be used for a new company and I attach a logo concept for your consideration.

```html
<!DOCTYPE html>
<html lang="en">
<head>
<meta charset="utf-8">
<title>Bramblecrest Carton Works – Presentation Template</title>
<link href="https://fonts.googleapis.com/css2?family=Roboto:wght@400;700;900&display=swap" rel="stylesheet">
<style>
  :root{
    --stage:#595959;
    --white:#ffffff;
    --green-dark:#0d6b3a;
    --green:#1fa34f;
    --green-light:#7fd39a;
    --lime:#c8dc1e;
    --ink:#1d1d1d;
    --grey-text:#555555;
  }
  *{box-sizing:border-box;margin:0;padding:0}
  html,body{width:847px;height:1200px;overflow:hidden;background:var(--stage);font-family:"Roboto",Arial,sans-serif}
  .slide{position:absolute;left:62px;width:728px;background:var(--white);overflow:hidden}
  .slide--title{top:42px;height:517px}
  .slide--content{top:627px;height:530px}

  /* title slide */
  .title-graphic{position:absolute;left:0;top:0;width:728px;height:430px;
    background:
      radial-gradient(ellipse at 70% 35%, rgba(255,255,255,.85) 0%, rgba(255,255,255,0) 35%),
      linear-gradient(120deg,#f4faf6 0%,#dff1e5 30%,#5cc27f 55%,#0f8a45 75%,#0a5a2f 100%);}
  .title-bottom{position:absolute;left:0;top:0;width:728px;height:517px}
  .heading{position:absolute;left:34px;top:30px;font-size:44px;font-weight:900;color:var(--green-dark);letter-spacing:.5px}
  .subheading{position:absolute;left:36px;top:88px;font-size:24px;font-weight:700;color:var(--ink)}
  .intro{position:absolute;left:36px;top:130px;font-size:15px;line-height:19px;color:var(--ink)}
  .brand{position:absolute;font-weight:700;color:var(--green)}
  .slide--title .brand{left:36px;top:458px;font-size:24px}
  .presenter{position:absolute;right:26px;top:432px;font-size:10px;font-weight:700;color:var(--ink);line-height:12px}
  .presenter .date{display:block;margin-top:8px}
  .web{position:absolute;font-size:10px;font-weight:700;color:var(--green)}
  .slide--title .web{right:26px;top:490px}

  /* content slide */
  .band{position:absolute;left:0;top:0;width:728px;height:78px}
  .band-fill{position:absolute;left:0;top:0;width:728px;height:72px;
    background:linear-gradient(90deg,#0b6a37 0%,#1b9a4b 45%,#8fd8a5 75%,#eaf7ef 100%)}
  .content-heading{position:absolute;left:30px;top:16px;font-size:20px;font-weight:700;color:var(--white)}
  .content-sub{position:absolute;left:30px;top:42px;font-size:13px;color:var(--white)}
  .slide--content .brand{right:26px;top:40px;font-size:15px}
  .cubes{position:absolute;left:0;top:300px;width:728px;height:190px;
    background:linear-gradient(180deg,rgba(255,255,255,0) 0%,#e6e6e6 55%,#f2f2f2 100%)}
  .footer-line{position:absolute;left:0;top:498px;width:728px;height:1px;background:#dddddd}
  .slide--content .web{right:60px;top:507px}
  .page-no{position:absolute;right:26px;top:505px;font-size:11px;color:var(--grey-text)}
</style>
</head>
<body>
  <section class="slide slide--title">
    <div class="title-graphic" role="img" aria-label="Abstract green glassy layered shapes with light streaks"></div>
    <svg class="title-bottom" viewBox="0 0 728 517" aria-hidden="true">
      <path d="M0 430 C200 428 420 418 728 330 L728 517 L0 517 Z" fill="#ffffff"/>
      <path d="M0 426 C200 424 420 414 728 326" fill="none" stroke="#c8dc1e" stroke-width="5"/>
    </svg>
    <h1 class="heading">HEADING HERE</h1>
    <h2 class="subheading">SUBHEADING HERE</h2>
    <p class="intro">Example Slides For New Design PPT<br>Design Template</p>
    <div class="brand">Bramblecrest Carton Works</div>
    <div class="presenter">NAME OF THE<br>PRESENTERE<span class="date">Date : 00 00 00</span></div>
    <div class="web">www.bramblecrestcarton.com</div>
  </section>

  <section class="slide slide--content">
    <svg class="band" viewBox="0 0 728 78" aria-hidden="true">
      <rect x="0" y="70" width="728" height="4" fill="#c8dc1e"/>
    </svg>
    <div class="band-fill" role="img" aria-label="Green abstract glassy header strip"></div>
    <h2 class="content-heading">ADD YOUR HEADING HERE</h2>
    <p class="content-sub">Add your subheading here</p>
    <div class="brand">Bramblecrest Carton Works</div>
    <div class="cubes" role="img" aria-label="Faint transparent glass cubes scattered on a white floor"></div>
    <div class="footer-line"></div>
    <div class="web">www.bramblecrestcarton.com</div>
    <div class="page-no">01</div>
  </section>
</body>
</html>
```